Construction company business card

One side to be the logo with the company name, The other side I would like: (Tomas verbick) Project manager 41 barrow crescent hallam 52917306224783(03) 9703 2428Info@gudeljgroup.comAnd then maybe a couple dot points saying what we do:Construction (commercial & industrial) Civil construction

Anything else please contact me!
Maybe curved st one edge of the card

Target Market(s)

Older clientele

Industry/Entity Type

Construction Company

Contact Information for Business Card

Read above

Colors
3277b5
1b1b1b
9d9d9d

Requirements
Must have
• Use my logo on one side
Nice to have
• Read above
Should not have
• Read above

```html
<!DOCTYPE html>
<html lang="en">
<head>
<meta charset="utf-8">
<title>Stonecrest Property Group – Business Card</title>
<link rel="stylesheet" href="https://fonts.googleapis.com/css2?family=Open+Sans:wght@400;600;700&display=swap">
<style>
  :root {
    --brand-blue: #3277b5;
    --ink: #1b1b1b;
    --steel: #9d9d9d;
    --paper: #fbfbfb;
    --backdrop: #d9d9dc;
    --navy-top: #24384a;
    --navy-bottom: #142230;
    --rule: #e2e2e2;
    --light-text: #e8eef4;
  }
  * { box-sizing: border-box; margin: 0; padding: 0; }
  html, body {
    width: 1200px;
    height: 844px;
    overflow: hidden;
  }
  body {
    background: var(--backdrop);
    font-family: "Open Sans", Arial, sans-serif;
    position: relative;
  }
  .card {
    position: absolute;
    top: 262px;
    width: 530px;
    height: 320px;
    border-radius: 6px;
    box-shadow: 0 10px 30px rgba(0,0,0,0.18);
    overflow: hidden;
  }
  /* Contact side */
  .card--contact {
    left: 45px;
    background: var(--paper);
  }
  .brand {
    position: absolute;
    right: 36px;
    top: 46px;
    display: flex;
    align-items: center;
    gap: 10px;
  }
  .brand__dot {
    flex: 0 0 auto;
    width: 30px;
    height: 30px;
    border-radius: 50%;
    background: var(--brand-blue);
  }
  .brand__name {
    font-weight: 700;
    font-size: 19px;
    letter-spacing: 0.5px;
    color: var(--brand-blue);
    text-transform: uppercase;
    line-height: 1.1;
    white-space: nowrap;
  }
  .divider {
    position: absolute;
    left: 36px;
    right: 36px;
    top: 118px;
    height: 1px;
    background: var(--rule);
  }
  .person {
    position: absolute;
    left: 40px;
    top: 140px;
    color: var(--ink);
  }
  .person__name {
    font-size: 21px;
    font-weight: 700;
    color: var(--brand-blue);
    text-transform: uppercase;
    letter-spacing: 0.3px;
  }
  .person__role {
    font-size: 14px;
    margin-top: -2px;
  }
  .person__address {
    font-size: 14px;
    margin-top: 14px;
  }
  .contact-line {
    font-size: 14px;
    margin-top: 14px;
    white-space: nowrap;
  }
  .contact-line__label {
    color: var(--brand-blue);
    font-weight: 600;
  }
  .contact-line__sep { color: var(--steel); margin: 0 4px; }
  .services {
    list-style: none;
    display: flex;
    gap: 16px;
    font-size: 15px;
    margin-top: 18px;
  }
  .services__item {
    display: flex;
    align-items: center;
    gap: 7px;
  }
  .services__item::before {
    content: "";
    flex: 0 0 auto;
    width: 9px;
    height: 9px;
    border-radius: 50%;
    background: var(--brand-blue);
  }
  /* Logo side */
  .card--logo {
    left: 625px;
    background: linear-gradient(160deg, var(--navy-top), var(--navy-bottom));
  }
  .card--logo .brand {
    right: auto;
    left: 50%;
    top: 50%;
    transform: translate(-50%, -50%);
    gap: 14px;
  }
  .card--logo .brand__dot { width: 40px; height: 40px; }
  .card--logo .brand__name { font-size: 26px; color: var(--light-text); }
</style>
</head>
<body>
  <section class="card card--contact" aria-label="Business card, contact side">
    <div class="brand">
      <span class="brand__dot"></span>
      <span class="brand__name">Stonecrest<br>Property Group</span>
    </div>
    <div class="divider"></div>
    <div class="person">
      <h1 class="person__name">Tomas Verbick</h1>
      <p class="person__role">Project Manager</p>
      <p class="person__address">41 Barrow Crescent, Kelvale, 5291</p>
      <p class="contact-line">
        <span class="contact-line__label">P:</span> 7306224783<span class="contact-line__sep">|</span><span class="contact-line__label">M:</span> (03) 9418 6573<span class="contact-line__sep">|</span><span class="contact-line__label">E:</span> Info@verbickgroup.com
      </p>
      <ul class="services">
        <li class="services__item">Commercial</li>
        <li class="services__item">Industrial</li>
        <li class="services__item">Civil</li>
      </ul>
    </div>
  </section>

  <section class="card card--logo" aria-label="Business card, logo side">
    <div class="brand">
      <span class="brand__dot"></span>
      <span class="brand__name">Stonecrest<br>Property Group</span>
    </div>
  </section>
</body>
</html>
```